Ridgeline Orchards Organic Cherry POS card 7x11

We are wanting to create a one-sided 7 x 11 organic cherry card that is eye catching and informative.This should be clear and easy to read and not cluttered. We use these cards as a display in grocery stores, demo stands, and other events to market Organic Ridgeline Sweet Orchards. We have a few facts that we would like displayed on the card (see attachment).

Target Market(s)

Consumers

Industry/Entity Type

Agriculture

Requirements
Must have
• Natural color palettes
• Easy to read
• Ridgeline Orchards
Nice to have
• Unique, realistic cherry design

```html
<!DOCTYPE html>
<html lang="en">
<head>
<meta charset="utf-8">
<title>Ridgeline Orchards – Organic Cherry Card</title>
<link rel="stylesheet" href="https://fonts.googleapis.com/css2?family=Quicksand:wght@700&family=Dancing+Script:wght@700&display=swap">
<style>
  :root {
    --page: #ffffff;
    --warm-light: #b49c7c;
    --warm-mid: #8a6a58;
    --warm-dark: #5e3434;
    --cherry: #7a1522;
    --cherry-deep: #3a0a14;
    --chalk: #ebe6e0;
    --ink: #1a1310;
    --ring: rgba(255, 255, 255, 0.55);
  }
  * { margin: 0; padding: 0; box-sizing: border-box; }
  html, body {
    width: 1200px; height: 880px; overflow: hidden;
    background: var(--page);
  }
  .card {
    position: relative;
    width: 1200px; height: 880px;
    background: var(--page);
  }
  .card__scene {
    position: absolute;
    left: 0; top: 58px; width: 1200px; height: 764px;
    background:
      radial-gradient(ellipse 150px 170px at 1000px 440px, var(--cherry-deep) 0%, rgba(58,10,20,0.9) 60%, rgba(58,10,20,0) 100%),
      radial-gradient(ellipse 160px 180px at 810px 500px, #9a2030 0%, var(--cherry) 45%, rgba(122,21,34,0) 100%),
      radial-gradient(ellipse 420px 300px at 260px 380px, var(--warm-light) 0%, rgba(180,156,124,0) 100%),
      linear-gradient(180deg, var(--warm-mid) 0%, #7d5c4e 45%, var(--warm-dark) 100%);
  }
  .brand {
    position: absolute;
    left: 380px; top: 110px;
    display: flex; align-items: center; gap: 16px;
    font-family: "Quicksand", sans-serif;
    font-weight: 700;
    font-size: 48px;
    color: var(--ink);
  }
  .brand__dot {
    width: 40px; height: 40px; border-radius: 50%;
    background: var(--ink);
  }
  .facts {
    position: absolute; left: 50px; top: 0;
    font-family: "Quicksand", sans-serif;
    font-weight: 700;
    font-size: 34px;
    line-height: 1;
    letter-spacing: 0.36em;
    color: var(--chalk);
  }
  .facts__line { position: absolute; left: 0; white-space: nowrap; }
  .benefits {
    position: absolute; left: 0; top: 0;
    font-family: "Dancing Script", cursive;
    font-weight: 700;
    font-size: 25px;
    line-height: 1;
    color: #ffffff;
  }
  .benefits__line { position: absolute; white-space: nowrap; }
  .benefits__ring { position: absolute; left: 776px; top: 442px; }
</style>
</head>
<body>
<main class="card">
  <div class="card__scene" role="img" aria-label="Soft-focus photograph of two glossy dark red cherries with water droplets hanging from their stems on a warm brown background"></div>

  <div class="brand">
    <span class="brand__dot"></span>
    <span class="brand__name">Ridgeline Orchards</span>
  </div>

  <div class="facts">
    <span class="facts__line" style="top:255px">Organic</span>
    <span class="facts__line" style="top:299px">Ridgeline cherries</span>
    <span class="facts__line" style="top:357px">make up 1/3</span>
    <span class="facts__line" style="top:416px">of the nation’s</span>
    <span class="facts__line" style="top:460px">production.</span>
    <span class="facts__line" style="top:545px">Washington State</span>
    <span class="facts__line" style="top:589px">is the nation’s</span>
    <span class="facts__line" style="top:633px">largest producer</span>
    <span class="facts__line" style="top:676px">&nbsp;of organic</span>
    <span class="facts__line" style="top:719px">cherries.</span>
  </div>

  <svg class="benefits__ring" width="310" height="310" viewBox="0 0 310 310" aria-hidden="true">
    <circle cx="155" cy="155" r="150" fill="none" stroke="var(--ring)" stroke-width="3"/>
  </svg>

  <div class="benefits">
    <span class="benefits__line" style="left:852px;top:462px">Health benefits:</span>
    <span class="benefits__line" style="left:896px;top:506px">fat free</span>
    <span class="benefits__line" style="left:784px;top:546px">source of vitamin C</span>
    <span class="benefits__line" style="left:736px;top:590px">a natural anti-inflammatory</span>
    <span class="benefits__line" style="left:840px;top:633px">source of potassium</span>
    <span class="benefits__line" style="left:812px;top:676px">source of melatonin</span>
  </div>
</main>
</body>
</html>
```